Business Card Design

We need a business card designed for our new company. Prefer a black card with white logo & writing.

Contact Information for Business Card

Ted Galloway, address: 7-4812 Fernhollow Road, Abbotsford, BC, V3K 8R2, Office Phone: 604-712-3390, Cell: 604-947-2164, Email: ted@resinworkshub.ca

Colors

Designer to choose only greyscale colors for use in the design.

```html
<!DOCTYPE html>
<html lang="en">
<head>
<meta charset="utf-8">
<title>Resin Works Hub – Business Card</title>
<link href="https://fonts.googleapis.com/css2?family=Montserrat:wght@400;600;700&display=swap" rel="stylesheet">
<style>
  :root {
    --backdrop: #d9d6d2;
    --card: #262626;
    --ink: #ffffff;
    --ink-soft: #e6e6e6;
    --shadow: rgba(0, 0, 0, 0.35);
  }
  * { margin: 0; padding: 0; box-sizing: border-box; }
  html, body {
    width: 900px;
    height: 1200px;
    overflow: hidden;
    background: var(--backdrop);
    font-family: "Montserrat", sans-serif;
    color: var(--ink);
  }
  .canvas { position: relative; width: 900px; height: 1200px; }
  .card {
    position: absolute;
    left: 80px;
    width: 740px;
    height: 440px;
    background: var(--card);
    border-radius: 24px;
    box-shadow: 0 6px 18px var(--shadow);
  }
  .card--front { top: 132px; }
  .card--back { top: 640px; }

  .brand {
    position: absolute;
    display: flex;
    flex-direction: column;
    align-items: center;
    font-weight: 700;
    color: var(--ink);
    text-transform: uppercase;
    line-height: 1;
  }
  .brand__mark {
    width: 22px;
    height: 22px;
    background: var(--ink);
    margin-bottom: 14px;
  }
  .card--front .brand { left: 100px; top: 188px; width: 250px; font-size: 30px; letter-spacing: 1px; }
  .card--back .brand { left: 170px; top: 168px; width: 400px; font-size: 48px; letter-spacing: 2px; }
  .card--back .brand__mark { width: 32px; height: 32px; margin-bottom: 20px; }
  .brand__line + .brand__line { margin-top: 8px; }

  .divider {
    position: absolute;
    left: 370px;
    top: 126px;
    width: 2px;
    height: 224px;
    background: var(--ink);
  }
  .contact { position: absolute; left: 392px; top: 124px; }
  .contact__name { font-size: 24px; font-weight: 700; letter-spacing: 0.3px; }
  .contact__role { font-size: 15px; font-weight: 400; color: var(--ink-soft); margin-top: 8px; }
  .contact__address { font-size: 15px; line-height: 20px; color: var(--ink-soft); margin-top: 16px; }
  .contact__list { list-style: none; margin-top: 14px; }
  .contact__item {
    display: flex;
    align-items: center;
    font-size: 15px;
    color: var(--ink-soft);
    height: 26px;
  }
  .contact__item + .contact__item { margin-top: 1px; }
  .contact__icon { width: 16px; height: 16px; margin-right: 12px; fill: var(--ink); flex: none; }
</style>
</head>
<body>
<main class="canvas">
  <section class="card card--front">
    <div class="brand">
      <span class="brand__mark"></span>
      <span class="brand__line">Resin Works</span>
      <span class="brand__line">Hub</span>
    </div>
    <div class="divider"></div>
    <div class="contact">
      <h1 class="contact__name">Ted Galloway</h1>
      <p class="contact__role">owner</p>
      <p class="contact__address">7-4812 Fernhollow Road,<br>Abbotsford, BC, V3K 8R2</p>
      <ul class="contact__list">
        <li class="contact__item">
          <svg class="contact__icon" viewBox="0 0 24 24" aria-hidden="true"><path d="M6.6 10.8a15.1 15.1 0 0 0 6.6 6.6l2.2-2.2c.3-.3.7-.4 1-.2 1.1.4 2.3.6 3.6.6.6 0 1 .4 1 1V20c0 .6-.4 1-1 1C10.6 21 3 13.4 3 4c0-.6.4-1 1-1h3.5c.6 0 1 .4 1 1 0 1.3.2 2.5.6 3.6.1.3 0 .7-.2 1z"/></svg>
          604-712-3390
        </li>
        <li class="contact__item">
          <svg class="contact__icon" viewBox="0 0 24 24" aria-hidden="true"><path d="M7 1h10a2 2 0 0 1 2 2v18a2 2 0 0 1-2 2H7a2 2 0 0 1-2-2V3a2 2 0 0 1 2-2zm0 3v14h10V4zm5 15.5a1 1 0 1 0 0 2 1 1 0 0 0 0-2z"/></svg>
          604-947-2164
        </li>
        <li class="contact__item">
          <svg class="contact__icon" viewBox="0 0 24 24" aria-hidden="true"><path d="M2 5h20v14H2zm2 2v.4l8 5 8-5V7z"/></svg>
          ted@resinworkshub.ca
        </li>
        <li class="contact__item">
          <svg class="contact__icon" viewBox="0 0 24 24" aria-hidden="true"><path d="M12 2a10 10 0 1 0 0 20 10 10 0 0 0 0-20zm-1 17.9A8 8 0 0 1 4.2 10L9 14.8V16a2 2 0 0 0 2 2zm6.9-2.5A2 2 0 0 0 16 16h-1v-3a1 1 0 0 0-1-1H8v-2h2a1 1 0 0 0 1-1V7h2a2 2 0 0 0 2-2v-.4a8 8 0 0 1 2.9 12.8z"/></svg>
          www.resinworkshub.ca
        </li>
      </ul>
    </div>
  </section>

  <section class="card card--back">
    <div class="brand">
      <span class="brand__mark"></span>
      <span class="brand__line">Resin Works</span>
      <span class="brand__line">Hub</span>
    </div>
  </section>
</main>
</body>
</html>
```